Fun, Clean Business Card For Family Focused Travel Agency

I need a business card using specific colors and fonts as in the uploaded files. Ideally, I would like a large image of the logo on the back and all the contact info on the front. Maybe the stars/dots somewhere in a flowy form.

I do want it the contact information to be clear and easy to read. I don't want it to look too busy. Maybe even a bit minimalist.

I plan or ordering the ROUNDED CORNER business cards from Cardwell Press, so please consider that in your design.

Target Market(s)

Families with children, couples, groups of friends

Contact Information for Business Card

Marla Quint, Owner
Marla@TumbleTrips.example
Cell Phone Number 555-218-4603
Office Phone Number 555-647-1925
Specializing in Glimmerland destinations, Pelican Bay Fun Park, Cruises and All-Inclusive Vacations.

Nice but not required:
www.TumbleTrips.example
Facebook, Instagram, Twitter icons with username: TumbleTrips

Font styles to use
Sans Serif

Requirements
Must have
• Please try to use the colors from the logo as much as possible. I understand lighter shades/colors may be needed for some things.
Should not have
• NO SERIF FONTS. That is really the only thing I do not want at all

```html
<!DOCTYPE html>
<html lang="en">
<head>
<meta charset="utf-8">
<title>TumbleTrips Business Card</title>
<link href="https://fonts.googleapis.com/css2?family=Open+Sans:wght@400;600;700&family=Dancing+Script:wght@700&display=swap" rel="stylesheet">
<style>
  :root{
    --stage:#2b2b2d;
    --navy:#0e1740;
    --navy-deep:#0a1030;
    --teal:#17ad8f;
    --ink:#1c1f3a;
    --text:#4a4a4a;
    --rule:#9a9a9a;
    --band-rule:#d8d8d8;
    --white:#ffffff;
  }
  *{box-sizing:border-box;margin:0;padding:0}
  html,body{width:1200px;height:892px;overflow:hidden}
  body{background:var(--stage);font-family:"Open Sans",Arial,sans-serif;position:relative}

  .card{position:absolute;width:580px;height:331px;border-radius:14px;overflow:hidden;box-shadow:0 10px 28px rgba(0,0,0,.45)}

  /* back side */
  .card-back{left:50px;top:70px;background:linear-gradient(150deg,var(--navy) 0%,var(--navy-deep) 100%);color:var(--white);text-align:center}
  .social{position:absolute;top:20px;right:24px;display:flex;gap:5px}
  .social span{width:13px;height:13px;border-radius:50%;background:var(--white)}
  .back-brand{position:absolute;left:0;right:0;top:58px;display:flex;flex-direction:column;align-items:center;gap:12px}
  .back-dot{width:64px;height:64px;border-radius:50%;background:var(--teal)}
  .back-name{font-size:26px;font-weight:700;color:var(--white);line-height:1}
  .specializing{position:absolute;left:0;right:0;top:178px;font-family:"Dancing Script",cursive;font-size:26px;line-height:1.2}
  .services{position:absolute;left:0;right:0;top:226px;font-size:14.5px;line-height:1.5;letter-spacing:.2px}

  /* front side */
  .card-front{left:570px;top:480px;background:var(--white)}
  .brand{position:absolute;right:34px;top:40px;display:flex;align-items:center;gap:14px}
  .brand-dot{width:58px;height:58px;border-radius:50%;background:var(--teal)}
  .brand-name{font-size:40px;font-weight:700;color:var(--ink);letter-spacing:-.5px;line-height:1}
  .divider{position:absolute;left:30px;right:30px;top:132px;height:1px;background:var(--rule)}
  .web{position:absolute;right:30px;top:148px;text-align:right;font-size:14px;color:var(--text);line-height:1.55}
  .web li,.phones li{list-style:none;display:flex;align-items:center;gap:8px}
  .web li{justify-content:flex-end}
  .line-icon{width:14px;height:14px;flex:none}
  .person{position:absolute;left:30px;top:196px}
  .name{font-size:23px;font-weight:700;color:var(--teal);letter-spacing:.5px;line-height:1.1}
  .role{font-size:14px;font-weight:600;color:var(--ink);letter-spacing:.4px;margin-bottom:8px}
  .phones{font-size:15px;color:var(--text);line-height:1.5}
  .band-rule{position:absolute;left:0;right:0;bottom:22px;height:3px;background:var(--band-rule)}
  .band{position:absolute;left:0;right:0;bottom:0;height:18px;background:var(--teal)}
</style>
</head>
<body>

<section class="card card-back">
  <div class="social" aria-label="Social links"><span></span><span></span><span></span></div>
  <div class="back-brand">
    <span class="back-dot" aria-hidden="true"></span>
    <span class="back-name">TumbleTrips</span>
  </div>
  <p class="specializing">Specializing in</p>
  <p class="services">Glimmerland destinations • Pelican Bay Fun Park<br>Cruises &amp; All-Inclusive Vacations.</p>
</section>

<section class="card card-front">
  <div class="brand">
    <span class="brand-dot" aria-hidden="true"></span>
    <span class="brand-name">TumbleTrips</span>
  </div>
  <div class="divider"></div>
  <ul class="web">
    <li>Marla@TumbleTrips.example
      <svg class="line-icon" viewBox="0 0 14 14" aria-hidden="true"><rect x="1" y="3" width="12" height="8" rx="1" fill="var(--teal)"/><path d="M1.5 3.5 7 8l5.5-4.5" stroke="#fff" stroke-width="1.2" fill="none"/></svg></li>
    <li>www.TumbleTrips.example
      <svg class="line-icon" viewBox="0 0 14 14" aria-hidden="true"><circle cx="7" cy="7" r="6" fill="var(--teal)"/><path d="M7 3.5a2.3 2.3 0 0 1 2.3 2.3C9.3 7.6 7 10.5 7 10.5S4.7 7.6 4.7 5.8A2.3 2.3 0 0 1 7 3.5z" fill="#fff"/></svg></li>
  </ul>
  <div class="person">
    <h1 class="name">MARLA QUINT</h1>
    <p class="role">OWNER</p>
    <ul class="phones">
      <li><svg class="line-icon" viewBox="0 0 14 14" aria-hidden="true"><path d="M2 5c0-2 2-3 5-3s5 1 5 3l-2 1-1-2H5L4 6z" fill="var(--teal)"/><rect x="3" y="7" width="8" height="5" rx="1" fill="var(--teal)"/></svg>555-647-1925</li>
      <li><svg class="line-icon" viewBox="0 0 14 14" aria-hidden="true"><rect x="3.5" y="1" width="7" height="12" rx="1.5" fill="none" stroke="var(--teal)" stroke-width="1.6"/><circle cx="7" cy="10.5" r=".9" fill="var(--teal)"/></svg>555-218-4603</li>
    </ul>
  </div>
  <div class="band-rule"></div>
  <div class="band"></div>
</section>

</body>
</html>
```